Coastline Premier Retreats Business Card Design

Design a business card for Coastline Premier Retreats. Look at the website for colors and reference. Card should have logo, name, title, office number, mobile number, email, URL and a tagline like, "Luxury Hotel & Resort Email Marketing" (This might change).

https://www.coastlinepremierretreats.example

The rest I will leave up to your imagination.

Contact Information for Business Card

Logo, name, title, office number, mobile number, email, URL and a tagline like, "Luxury Hotel & Resort Email Marketing" (This might change).

```html
<!DOCTYPE html>
<html lang="en">
<head>
<meta charset="utf-8">
<title>Coastline Premier Retreats – Business Card</title>
<link rel="stylesheet" href="https://fonts.googleapis.com/css2?family=Open+Sans:wght@400;600;700&display=swap">
<style>
  :root {
    --stage: #222223;
    --card-dark: #1f1f22;
    --orange: #f47623;
    --orange-deep: #d9611a;
    --white: #ffffff;
    --text-font: "Open Sans", Arial, sans-serif;
  }
  * { box-sizing: border-box; margin: 0; padding: 0; }
  html, body {
    width: 1200px; height: 780px; overflow: hidden;
    background: var(--stage);
    font-family: var(--text-font);
  }
  .stage {
    position: relative; width: 1200px; height: 780px;
    display: flex; align-items: center; justify-content: center; gap: 40px;
  }
  .card {
    position: relative; width: 540px; height: 310px;
    border-radius: 22px; overflow: hidden;
  }
  /* Back side */
  .card-back {
    background: var(--orange);
    display: flex; align-items: center; justify-content: center;
  }
  .back-wordmark {
    color: var(--orange-deep);
    font-weight: 700; font-size: 30px; letter-spacing: 1px;
    text-transform: uppercase; text-align: center; line-height: 1.15;
  }
  /* Front side */
  .card-front {
    background: var(--card-dark);
    border: 4px solid var(--orange);
    color: var(--white);
  }
  .brand {
    position: absolute; left: 30px; top: 30px;
    display: flex; align-items: center; gap: 10px;
  }
  .brand-mark { width: 14px; height: 14px; background: var(--orange); }
  .brand-name {
    color: var(--white); font-weight: 700; font-size: 19px;
    letter-spacing: 0.5px; text-transform: uppercase; line-height: 1.1;
  }
  .person {
    position: absolute; right: 40px; top: 78px; text-align: right;
  }
  .person-name { font-size: 26px; font-weight: 700; line-height: 1.1; }
  .person-name .first { color: var(--orange); }
  .person-name .last { color: var(--white); }
  .person-title { font-size: 14px; font-weight: 400; margin-top: 4px; }
  .accent-bar {
    position: absolute; right: 0; top: 74px;
    width: 22px; height: 62px; background: var(--orange);
  }
  .tagline {
    position: absolute; left: 30px; top: 170px;
    color: var(--orange); font-size: 14px; line-height: 1.3;
  }
  .contact-list {
    position: absolute; left: 30px; top: 214px; list-style: none;
  }
  .contact-list li {
    display: flex; align-items: center; gap: 10px;
    font-size: 13px; line-height: 19px;
  }
  .contact-list svg { width: 13px; height: 13px; flex: none; }
</style>
</head>
<body>
<main class="stage">

  <section class="card card-back" aria-label="Card back">
    <p class="back-wordmark">Coastline Premier<br>Retreats</p>
  </section>

  <section class="card card-front" aria-label="Card front">
    <div class="brand">
      <span class="brand-mark"></span>
      <span class="brand-name">Coastline Premier Retreats</span>
    </div>

    <div class="person">
      <p class="person-name"><span class="first">Marlena</span> <span class="last">Holloway</span></p>
      <p class="person-title">Managing Director</p>
    </div>
    <span class="accent-bar"></span>

    <p class="tagline">Luxury Hotel &amp;<br>Resort Email Marketing</p>

    <ul class="contact-list">
      <li>
        <svg viewBox="0 0 24 24" fill="var(--orange)"><path d="M6.6 10.8a15 15 0 0 0 6.6 6.6l2.2-2.2c.3-.3.7-.4 1-.2 1.1.4 2.3.6 3.6.6.6 0 1 .4 1 1V20c0 .6-.4 1-1 1A17 17 0 0 1 3 4c0-.6.4-1 1-1h3.5c.6 0 1 .4 1 1 0 1.3.2 2.5.6 3.6.1.3 0 .7-.2 1z"/></svg>
        (555) 214-3086
      </li>
      <li>
        <svg viewBox="0 0 24 24" fill="none" stroke="var(--orange)" stroke-width="2.5"><rect x="6" y="2" width="12" height="20" rx="2"/></svg>
        (555) 730-4419
      </li>
      <li>
        <svg viewBox="0 0 24 24" fill="none" stroke="var(--orange)" stroke-width="2.2"><circle cx="12" cy="12" r="10"/><path d="M2 12h20M12 2c3 3 3 17 0 20M12 2c-3 3-3 17 0 20"/></svg>
        www.coastlinepremierretreats.example
      </li>
      <li>
        <svg viewBox="0 0 24 24" fill="none" stroke="var(--orange)" stroke-width="2.2"><rect x="2" y="5" width="20" height="14" rx="1"/><path d="M2 6l10 7 10-7"/></svg>
        info@coastlinepremierretreats.example
      </li>
    </ul>
  </section>

</main>
</body>
</html>
```